Steadfast Field Crews

We are a underground coal mining labour hire company, needing a website that links into our online payroll (www.wagelinkr.com.au) and also need to have job applications page that is a preform with drop down menu,s with answers or check boxes. We would also need a 3 tier administration access for access to different files.
We are looking for an ongoing relationship with future app integration

Reason: There are a few more designs to come and I'm out at the mine for another week

Industry/Entity Type

Coal Mining

```html
<!DOCTYPE html>
<html lang="en">
<head>
<meta charset="utf-8">
<title>Steadfast Field Crews</title>
<link href="https://fonts.googleapis.com/css2?family=Ubuntu:wght@400;500;700&display=swap" rel="stylesheet">
<style>
:root{
  --orange:#f7801f;
  --orange-dark:#d86a12;
  --ink:#0e0d0c;
  --rock-1:#3a3733;
  --rock-2:#1e1c1a;
  --line:#6b4a2c;
  --text:#ecebe8;
  --muted:#8f8c87;
  --grey-icon:#77746f;
  --payroll:#34348a;
}
*{margin:0;padding:0;box-sizing:border-box}
html,body{width:1200px;height:1029px;overflow:hidden;background:var(--ink)}
body{font-family:'Ubuntu',sans-serif;color:var(--text);position:relative}
a{color:inherit;text-decoration:none}
.rock-backdrop{position:absolute;inset:0;background:radial-gradient(ellipse at 20% 30%,var(--rock-1),var(--rock-2) 70%)}
.page-column{position:absolute;left:163px;top:0;width:875px;height:1029px;background:rgba(10,9,8,.45)}
.header-band{position:absolute;left:0;top:0;width:1200px;height:97px;background:rgba(12,11,10,.85)}
.brand{position:absolute;left:192px;top:34px;display:flex;align-items:center;gap:10px}
.brand-dot{width:14px;height:14px;border-radius:50%;background:#fff}
.brand-name{font-size:24px;font-weight:500;color:#fff;line-height:1}
.account-links{position:absolute;left:906px;top:10px;width:102px;height:26px;background:#000;font-size:10.5px;display:flex;align-items:center;justify-content:center;gap:5px}
.main-nav{position:absolute;top:66px;left:484px;display:flex;font-size:10.5px}
.main-nav a{color:var(--text);margin-right:26px}
.main-nav a:last-child{margin-right:0}
.main-nav a.current{color:var(--orange);font-weight:700}
.main-nav .caret{display:inline-block;margin-left:5px;border:3px solid transparent;border-top:4px solid var(--muted);vertical-align:middle}
.hero{position:absolute;left:172px;top:97px;width:857px;height:328px;background:linear-gradient(100deg,#6b5a2e 0%,#4b4a44 35%,#3e3c38 65%,#2a2826 100%)}
.hero-title{position:absolute;right:42px;top:82px;text-align:right;font-size:29px;font-weight:700;color:#fff;line-height:1.25}
.hero-copy{position:absolute;right:42px;top:173px;width:400px;text-align:right;font-size:12.5px;font-weight:700;line-height:1.35;color:#fff}
.hero-scroller{position:absolute;left:832px;top:86px;width:3px;height:167px;background:#555}
.hero-scroller span{position:absolute;left:0;top:86px;width:3px;height:38px;background:var(--orange)}
.feature-tile{position:absolute;top:428px;height:110px;border-radius:0 0 8px 8px;background:#0d0c0b;border:1px solid #2d2b28;display:flex;align-items:center;justify-content:center;gap:14px}
.feature-tile.payroll{left:172px;width:283px;top:425px;height:113px;background:#fff;border:2px solid var(--orange);border-radius:6px;flex-direction:column;gap:2px}
.payroll-kicker{font-size:11.5px;font-weight:500;color:var(--orange)}
.payroll-name{display:flex;align-items:center;gap:8px;font-size:36px;color:var(--payroll);line-height:1}
.payroll-name i{width:22px;height:22px;background:var(--payroll)}
.feature-tile.jobs{left:460px;width:281px}
.feature-tile.benefits{left:747px;width:282px}
.tile-label{font-size:17px;font-weight:500;color:var(--grey-icon);line-height:1.3}
.welcome{position:absolute;left:172px;top:551px;width:857px;height:246px;border:1px solid #4a4640;border-bottom:none;background:rgba(18,16,14,.55)}
.welcome h1{position:absolute;left:30px;top:30px;font-size:26px;font-weight:700;color:var(--orange);line-height:1.3;width:520px}
.welcome p{position:absolute;left:30px;top:110px;width:560px;font-size:12.8px;line-height:1.32}
.btn-primary{position:absolute;left:28px;top:174px;width:228px;height:43px;background:var(--orange);border-bottom:3px solid var(--orange-dark);display:flex;align-items:center;justify-content:center;font-size:13px;color:#fff}
.emblem{position:absolute;left:623px;top:14px;width:195px;height:217px;border-radius:50%;background:radial-gradient(circle,#f7801f 0%,#7a3d10 45%,transparent 72%)}
.info-card{position:absolute;top:797px;height:130px;border:1px solid var(--line);background:rgba(14,12,10,.6)}
.info-card h2{position:absolute;left:27px;top:24px;font-size:18px;font-weight:700;color:var(--orange)}
.info-card .card-icon{position:absolute;right:24px;top:26px}
.info-card p{position:absolute;left:27px;top:54px;width:215px;font-size:12.6px;line-height:1.35}
.info-card .date{color:var(--muted)}
.service-list{position:absolute;left:25px;top:54px;list-style:none;font-size:12.6px;line-height:1.35}
.service-list li{display:flex;gap:6px;margin-bottom:8px}
.service-list li::before{content:"";flex:none;width:13px;height:13px;border:1.5px solid var(--orange);border-radius:50%;margin-top:1px}
.card-news{left:172px;width:276px}
.card-services{left:463px;width:276px}
.card-engineering{left:754px;width:275px}
.btn-small{position:absolute;top:927px;width:91px;height:24px;background:var(--orange);border-bottom:2px solid var(--orange-dark);font-size:12px;color:#fff;display:flex;align-items:center;justify-content:center}
.site-footer{position:absolute;left:172px;top:970px;width:857px;height:50px;background:rgba(10,9,8,.8);display:flex;align-items:center;justify-content:center;font-size:12.8px}
</style>
</head>
<body>
<div class="rock-backdrop" role="img" aria-label="Dark underground rock wall photograph"></div>
<div class="page-column"></div>

<header class="header-band">
  <div class="brand"><span class="brand-dot"></span><span class="brand-name">Steadfast Field Crews</span></div>
  <div class="account-links"><span>Login</span><span>|</span><span>Register</span></div>
  <nav class="main-nav">
    <a class="current">HOME</a><a>APPLICATION</a><a>PAY PORTAL</a><a>INFORMATION<span class="caret"></span></a><a>ABOUT US</a><a>CONTACT</a><a>MISSION</a>
  </nav>
</header>

<section class="hero" role="img" aria-label="Photograph of miners in safety gear working in an underground tunnel">
  <h2 class="hero-title">ROADHEADER DRIVAGE /<br>TUNNEL EXCAVATION</h2>
  <p class="hero-copy">we are experienced in ground consolidation in underground coal mines, in short when they collapse or cave in we come in with chemical pumps and stabilise the ground or fill cavities which will then allow for the mining process to continue. We also do general mine labor as well.</p>
  <div class="hero-scroller"><span></span></div>
</section>

<a class="feature-tile payroll">
  <span class="payroll-kicker">Our online payroll</span>
  <span class="payroll-name"><i></i>wagelinkr</span>
</a>
<a class="feature-tile jobs">
  <svg width="58" height="54" viewBox="0 0 58 54" fill="none" stroke="var(--grey-icon)" stroke-width="3"><rect x="2" y="2" width="44" height="34" rx="2"/><line x1="10" y1="44" x2="34" y2="44"/><line x1="24" y1="12" x2="40" y2="12"/><line x1="24" y1="19" x2="40" y2="19"/><rect x="8" y="9" width="12" height="10" fill="var(--grey-icon)"/><circle cx="42" cy="38" r="8"/><line x1="48" y1="44" x2="55" y2="51"/></svg>
  <span class="tile-label">Our Job<br>Vacancies</span>
</a>
<a class="feature-tile benefits">
  <svg width="54" height="60" viewBox="0 0 54 60" fill="var(--grey-icon)"><circle cx="12" cy="26" r="6"/><path d="M2 46c0-8 5-12 10-12s10 4 10 12z"/><rect x="34" y="2" width="16" height="56"/><rect x="26" y="18" width="8" height="3"/><rect x="26" y="38" width="8" height="3"/></svg>
  <span class="tile-label">Employee<br>Benifit<br>Programs</span>
</a>

<section class="welcome">
  <h1>WELCOME TO STEADFAST FIELD<br>CREWS</h1>
  <p>we are experienced in ground consolidation in underground coal mines, in short when they collapse or cave in we come in with chemical pumps and stabilise the ground or fill cavities which will then allow for the mining process to continue. We also do general mine labor as well.</p>
  <a class="btn-primary">LEARN MORE</a>
  <div class="emblem" role="img" aria-label="Orange illustrated miner emblem badge"></div>
</section>

<article class="info-card card-news">
  <h2>News</h2>
  <svg class="card-icon" width="18" height="18" viewBox="0 0 18 18" fill="none" stroke="var(--orange)" stroke-width="2"><rect x="3" y="5" width="12" height="9" transform="rotate(-35 9 9)"/></svg>
  <p>we are experienced in ground consolidation in underground coal mines.... <span class="date">12-12-2013</span></p>
</article>
<a class="btn-small" style="left:357px">LEARN MORE</a>

<article class="info-card card-services">
  <h2>Services</h2>
  <svg class="card-icon" width="18" height="18" viewBox="0 0 18 18" fill="none" stroke="var(--orange)" stroke-width="2.5"><circle cx="6" cy="12" r="3.5"/><circle cx="13" cy="5" r="2.5"/></svg>
  <ul class="service-list"><li>Roadheader Drivage / Tunnel<br>Excavation</li><li>Labour Hire</li></ul>
</article>
<a class="btn-small" style="left:648px">LEARN MORE</a>

<article class="info-card card-engineering">
  <h2>Engineering</h2>
  <svg class="card-icon" width="18" height="18" viewBox="0 0 18 18" fill="var(--orange)"><path d="M2 11a7 7 0 0 1 14 0z"/><rect x="1" y="11" width="16" height="2"/></svg>
  <p>Lorem ipsum dolor sit amet, consectetuer adipiscing elit, sed diam nonummy ...</p>
</article>
<a class="btn-small" style="left:938px">LEARN MORE</a>

<footer class="site-footer">©2014 Steadfast Field Crews – Underground Construction – Coal Mine Services</footer>
</body>
</html>
```